Business Folder

I need a fresh, modern design for a business folder. I have our company's colors, logo, and a separate file for just the graphic part of our logo as a design element. No photo, just colors, gradients, and shadows to create depth. I like the idea of a rich grey as the background, however, I realize we'd have to lighten to 'Tax Advisory Services' part of our logo.

The design would just be the 'front' or outside of the folder from PressVale. Design file attached. You can find that here under 9 x 12 standard folder, Left and Right Pockets With Slit Both Sides:

https://www.pressvale-example.com/content.html?id=folderDownloadTemplates&rightMenuId=rightMenu&footerId=bodyFooterStyle6

```html
<!DOCTYPE html>
<html lang="en">
<head>
<meta charset="utf-8">
<title>Lumen Tax Advisory Services – Business Folder</title>
<link href="https://fonts.googleapis.com/css2?family=Montserrat:wght@400;600;800&display=swap" rel="stylesheet">
<style>
  :root {
    --stage: #e2e2e2;
    --folder-grey: #6e6d6e;
    --paper: #ffffff;
    --soft-white: #f3f3f3;
    --ink-light: #e9e9e9;
    --brand-blue: #1f5d96;
  }
  * { margin: 0; padding: 0; box-sizing: border-box; }
  html, body { width: 1200px; height: 1200px; overflow: hidden; }
  body {
    background: var(--stage);
    font-family: "Montserrat", sans-serif;
    position: relative;
  }
  .spread {
    position: absolute;
    left: 270px;
    width: 660px;
    height: 440px;
    display: flex;
    box-shadow: 0 14px 30px rgba(0,0,0,0.18);
  }
  .spread--outside { top: 70px; }
  .spread--inside { top: 670px; }
  .panel { position: relative; width: 330px; height: 440px; overflow: hidden; }
  .panel--grey { background: var(--folder-grey); color: var(--paper); }
  .panel--white { background: var(--paper); }
  .panel svg.pocket { position: absolute; inset: 0; }

  .spine-band {
    position: absolute; top: 0; right: 0; width: 48px; height: 100%;
    background: linear-gradient(90deg, var(--paper) 0%, var(--soft-white) 70%, #d9d9d9 100%);
  }

  .wordmark { position: absolute; display: flex; align-items: center; gap: 7px; color: inherit; }
  .wordmark__square { width: 16px; height: 16px; background: currentColor; }
  .wordmark__text { display: flex; flex-direction: column; line-height: 1; }
  .wordmark__name { font-weight: 800; font-size: 26px; letter-spacing: 1px; }
  .wordmark__sub { font-weight: 400; font-size: 6.5px; letter-spacing: 1.2px; margin-top: 3px; text-transform: uppercase; }

  .front-logo { top: 40px; left: 150px; }
  .back-logo { top: 258px; left: 80px; }
  .pocket-logo { top: 355px; left: 100px; color: var(--paper); }

  .tagline {
    position: absolute; left: 100px; top: 300px;
    font-weight: 800; font-size: 15px; line-height: 1.25; white-space: nowrap;
  }
  .tagline-rule {
    position: absolute; left: 100px; top: 372px; width: 205px; height: 1px;
    background: rgba(255,255,255,0.55);
  }
  .front-url {
    position: absolute; left: 100px; top: 382px; width: 205px; text-align: right;
    font-size: 7.5px; letter-spacing: 1px; color: var(--ink-light);
  }

  .contact {
    position: absolute; top: 338px; font-size: 6.3px; line-height: 1.5; color: var(--ink-light);
    list-style: none; white-space: nowrap;
  }
  .contact li { display: flex; align-items: flex-start; gap: 4px; margin-bottom: 3px; }
  .contact strong { font-weight: 600; color: var(--paper); }
  .contact svg { flex: none; margin-top: 1px; }
  .contact--address { left: 14px; width: 142px; }
  .contact--lines { left: 164px; width: 112px; }

  .business-card {
    position: absolute; left: 130px; top: 262px; width: 170px; height: 92px;
    background: var(--paper); color: var(--brand-blue);
    box-shadow: 0 2px 6px rgba(0,0,0,0.2);
  }
  .business-card .wordmark { top: 24px; left: 38px; }
  .business-card .wordmark__name { font-size: 20px; }
  .business-card .wordmark__square { width: 12px; height: 12px; }
  .business-card .wordmark__sub { font-size: 5px; }
  .card-url {
    position: absolute; left: 0; right: 0; top: 64px; text-align: center;
    font-size: 7px; font-weight: 600; letter-spacing: 0.6px;
  }
  .inner-fold {
    position: absolute; top: 0; right: 0; width: 40px; height: 100%;
    background: linear-gradient(90deg, rgba(0,0,0,0) 0%, rgba(0,0,0,0.08) 100%);
  }
</style>
</head>
<body>

<section class="spread spread--outside" aria-label="Folder outside">
  <div class="panel panel--grey back-cover">
    <div class="spine-band"></div>
    <div class="wordmark back-logo">
      <span class="wordmark__square"></span>
      <span class="wordmark__text">
        <span class="wordmark__name">LUMEN</span>
        <span class="wordmark__sub">Tax Advisory Services</span>
      </span>
    </div>
    <ul class="contact contact--address">
      <li>
        <svg width="8" height="8" viewBox="0 0 10 10"><path d="M5 0C3 0 1.5 1.5 1.5 3.4 1.5 6 5 10 5 10s3.5-4 3.5-6.6C8.5 1.5 7 0 5 0z" fill="#fff"/></svg>
        <span><strong>Lumen Tax Advisory Services, LLC</strong><br>1420 Orchard Lane, Ste. 210<br>Fairview, IA 50000</span>
      </li>
      <li>
        <svg width="8" height="8" viewBox="0 0 10 10"><path d="M2 0l2 2.5-1 1.2c.7 1.4 1.8 2.5 3.2 3.2l1.2-1L10 8l-1.5 2C4 9.5.5 6 0 1.5z" fill="#fff"/></svg>
        <span>515-555-0187</span>
      </li>
    </ul>
    <ul class="contact contact--lines">
      <li>
        <svg width="8" height="8" viewBox="0 0 10 10"><path d="M2 0l2 2.5-1 1.2c.7 1.4 1.8 2.5 3.2 3.2l1.2-1L10 8l-1.5 2C4 9.5.5 6 0 1.5z" fill="#fff"/></svg>
        <span>800-555-0142</span>
      </li>
      <li>
        <svg width="8" height="8" viewBox="0 0 10 10"><rect x="0.5" y="2" width="9" height="6" fill="none" stroke="#fff"/><path d="M0.5 2L5 5.5 9.5 2" fill="none" stroke="#fff"/></svg>
        <span>info@lumentaxadvisory.com</span>
      </li>
      <li>
        <svg width="8" height="8" viewBox="0 0 10 10"><circle cx="5" cy="5" r="4.4" fill="none" stroke="#fff"/><path d="M0.6 5h8.8M5 0.6c-2.4 2.6-2.4 6.2 0 8.8M5 0.6c2.4 2.6 2.4 6.2 0 8.8" fill="none" stroke="#fff" stroke-width="0.7"/></svg>
        <span>www.LumenTaxAdvisory.com</span>
      </li>
    </ul>
  </div>

  <div class="panel panel--grey front-cover">
    <div class="wordmark front-logo">
      <span class="wordmark__square"></span>
      <span class="wordmark__text">
        <span class="wordmark__name">LUMEN</span>
        <span class="wordmark__sub">Tax Advisory Services</span>
      </span>
    </div>
    <p class="tagline">We’ll review your<br>options &amp; provide you<br>with tax-saving strategies.</p>
    <div class="tagline-rule"></div>
    <p class="front-url">www.LumenTaxAdvisory.com</p>
  </div>
</section>

<section class="spread spread--inside" aria-label="Folder inside">
  <div class="panel panel--white left-inside">
    <div class="inner-fold"></div>
    <svg class="pocket" viewBox="0 0 330 440" width="330" height="440">
      <path d="M0 440 V312 Q120 250 255 272 Q300 282 330 300 V440 Z" fill="var(--folder-grey)"/>
    </svg>
    <div class="wordmark pocket-logo">
      <span class="wordmark__square"></span>
      <span class="wordmark__text">
        <span class="wordmark__name">LUMEN</span>
        <span class="wordmark__sub">Tax Advisory Services</span>
      </span>
    </div>
  </div>

  <div class="panel panel--white right-inside">
    <svg class="pocket" viewBox="0 0 330 440" width="330" height="440">
      <path d="M36 440 V300 Q36 232 104 232 H330 V440 Z" fill="var(--folder-grey)"/>
    </svg>
    <div class="business-card">
      <div class="wordmark">
        <span class="wordmark__square"></span>
        <span class="wordmark__text">
          <span class="wordmark__name">LUMEN</span>
          <span class="wordmark__sub">Tax Advisory Services</span>
        </span>
      </div>
      <p class="card-url">www.LumenTaxAdvisory.com</p>
    </div>
  </div>
</section>

</body>
</html>
```